Bright and beautiful business card for a coach

I'm a personal and business coach based in Perth, Australia. I need a business card that whilst subtle and elegant, will stand out and appeal on a table full of cards.

My business name is Fern Mentoring and the business card must represent the warmth and brightness implied in the name, without being gimmicky. It must have a warmth and appeal and be easy to read.

I prefer clean, minimalist designs.

It must align with the feel of my website and socials: https://www.fernmentoring-example.com.au/
https://www.instagram.com/fernmentoringau/
https://www.facebook.com/fernmentoringau
Updates

Hi Designers Thank you so much for taking the time to submit designs. I wonder if I could have explained myself a little better. Most of the designs that have been submitted look rather formal and many have quite corporate looking embellishments on them (to my eye). I would like softer, warmer, more organic. I’m open to people playing about and being more abstract, using softer embellishments (e.g the line drawing flowers and grasses I’ve used in my socials) incorporating other colours from my palette or like the social icons in my email signature (in PDF), perhaps playing with size/oversize, playing with the bleed. Please don’t be constrained by what I’ve already done, it merely needs to compliment. I’m sorry if I’m not using the right words or have led you astray. I’m no designer, but I’ve done my website, socials, email signature etc all myself (my logo was a design contest) and I was really hoping for my business card to be something more creative than I could have made with a template. Reminder: No black cards/sides please. Thank you 😊

Target Market(s)

Individuals, most likely but not all female. Creative thinkers. Likely professionals.

Industry/Entity Type

Business & Personal Coach

Contact Information for Business Card

(Fern Mentoring Logo) Name: Greta Pellham; Title: Business & Personal Coach; Phone number: +61 (0)458 913307; Email: greta@fernmentoring-example.com.au; Website: https://fernmentoring-example.com.au; Social icons for Facebook, Instagram & LinkedIn: @fernmentoringAU. Optional strapline: "A thinking partner to help you cut through the noise"

Font styles to use
Sans Serif

Colors
00AB8E
00BBA5
67D7C9
C6EFE9
E9F9F6
59FF00
82FF00
B8FF75
E3FFCB
F4FFEA
FFC000
F8CF3A
FAE287
FDF2CF
FEFAEE

Requirements
Must have
• Must align with feel of my website and socials. Must have a pop of #FFC000 (possibly whole of one side, or at least a block). Bright or white background. Easy to read.
Nice to have
• Possibly incorporate the sunshine/grass picture I have used in website and socials - will upload.
Should not have
• Must not be black or dark. Not impersonal or corporate looking.

```html
<!DOCTYPE html>
<html lang="en">
<head>
<meta charset="utf-8">
<title>Fern Mentoring – Business Card</title>
<link href="https://fonts.googleapis.com/css2?family=Great+Vibes&family=Lato:ital,wght@0,300;0,400;0,700;1,400&display=swap" rel="stylesheet">
<style>
  :root {
    --sun: #FBBE02;
    --paper: #FFFFFF;
    --ink: #5E6866;
    --page: #FFFFFF;
    --edge: #F2C230;
  }
  * { box-sizing: border-box; margin: 0; padding: 0; }
  html, body {
    width: 1200px; height: 1091px; overflow: hidden;
    background: var(--page);
  }
  .stage { position: relative; width: 1200px; height: 1091px; }

  .card {
    position: absolute;
    width: 694px; height: 398px;
    overflow: hidden;
  }

  /* Front side */
  .card--front {
    left: 129px; top: 174px;
    background: var(--sun);
    z-index: 2;
  }
  .front-decor { position: absolute; }
  .front-decor--top {
    left: 0; top: 0; width: 300px; height: 190px;
    background: radial-gradient(ellipse at 25% 20%, rgba(255,225,120,0.7), rgba(255,225,120,0) 70%);
  }
  .front-decor--bottom {
    right: 0; bottom: 0; width: 400px; height: 210px;
    background: radial-gradient(ellipse at 75% 85%, rgba(255,225,120,0.75), rgba(255,225,120,0) 72%);
  }
  .brand {
    position: absolute;
    left: 0; right: 0; top: 165px;
    text-align: center;
    font-family: "Lato", sans-serif;
    font-weight: 300;
    font-size: 46px;
    letter-spacing: 3px;
    color: var(--paper);
  }

  /* Back side */
  .card--back {
    left: 374px; top: 512px;
    background: var(--paper);
    border: 1px solid var(--edge);
    z-index: 1;
  }
  .back-decor {
    position: absolute;
    right: 0; bottom: 0; width: 380px; height: 190px;
    background: radial-gradient(ellipse at 80% 100%, var(--sun) 0%, rgba(251,190,2,0.55) 40%, rgba(251,190,2,0) 75%);
  }
  .contact {
    position: absolute;
    left: 35px; top: 92px;
    font-family: "Lato", sans-serif;
    color: var(--ink);
  }
  .contact__name {
    font-family: "Great Vibes", cursive;
    font-weight: 400;
    font-size: 62px;
    line-height: 1;
    color: var(--sun);
  }
  .contact__title {
    margin-top: 8px;
    font-weight: 300;
    font-size: 26px;
    letter-spacing: 0.5px;
  }
  .contact__list { list-style: none; margin-top: 14px; }
  .contact__item {
    display: flex; align-items: center; gap: 8px;
    font-size: 19px; line-height: 29px;
  }
  .contact__item--url { font-style: italic; }
  .contact__icon { width: 23px; height: 18px; flex: none; }
  .contact__social {
    display: flex; gap: 6px;
    margin-top: 8px;
  }
  .social-dot {
    width: 22px; height: 22px;
    border-radius: 4px;
    background: var(--sun);
  }
</style>
</head>
<body>
<main class="stage">

  <section class="card card--front" aria-label="Card front">
    <div class="front-decor front-decor--top" role="img" aria-label="Soft pale-yellow organic brush strokes"></div>
    <div class="front-decor front-decor--bottom" role="img" aria-label="Soft pale-yellow organic brush strokes"></div>
    <h1 class="brand">Fern Mentoring</h1>
  </section>

  <section class="card card--back" aria-label="Card back">
    <div class="back-decor" role="img" aria-label="Golden organic brush strokes rising from the corner"></div>
    <div class="contact">
      <h2 class="contact__name">Greta Pellham</h2>
      <p class="contact__title">Business &amp; Personal Coach</p>
      <ul class="contact__list">
        <li class="contact__item">
          <svg class="contact__icon" viewBox="0 0 24 18" aria-hidden="true"><rect x="0" y="1" width="24" height="16" rx="1.5" fill="#FBBE02"/><path d="M1 2 L12 10 L23 2" fill="none" stroke="#fff" stroke-width="2"/></svg>
          greta@fernmentoring-example.com.au
        </li>
        <li class="contact__item">
          <svg class="contact__icon" viewBox="0 0 24 24" aria-hidden="true"><path d="M5 2 L9 2 L10.5 7 L8 9 C9.5 12 12 14.5 15 16 L17 13.5 L22 15 L22 19 C22 21 20 22 18 22 C9 21 3 15 2 6 C2 4 3 2 5 2 Z" fill="#FBBE02"/></svg>
          +61 (0)458 913307
        </li>
        <li class="contact__item contact__item--url">https://fernmentoring-example.com.au</li>
        <li class="contact__item">@fernmentoringAU</li>
      </ul>
      <div class="contact__social" role="img" aria-label="Social profile markers">
        <span class="social-dot"></span>
        <span class="social-dot"></span>
        <span class="social-dot"></span>
      </div>
    </div>
  </section>

</main>
</body>
</html>
```